Business Card Design

We need a business card designed for a new company based in Melbourne called Kvt solutions. Kvt solutions provides management consulting specialising in the health and social services sector.

Kvt solutions offer a unique set of specialist skills │dealing with all levels of government │ unique communication skills│intimate knowledge of the health sector │solutions tailored to unique circumstances.

Kvt solutions takes on a select number of clients at any one time, this ensures that your organisation receives the attention required. On larger projects, Kvt solutions join up with other consultants to bring specialist skills to a project.
Updates

This is the first time I have used Pixel Harbor and thank you all for responding. The variation is amazing and makes it hard to decide. I have to ask some of my friends to give me their views. The response is fantastic. The one I pick will basically be the most visually appealing

Industry/Entity Type

Management Consulting

Contact Information for Business Card

Martin Oakes, Principal, Kvt solutions, 14 Wexcombe Ave, Larkdale VIC 3189, 0417 382 914, martino@kvtsolutions-example.com.au, www.kvtsolutions-example.com.au

```html
<!DOCTYPE html>
<html lang="en">
<head>
<meta charset="utf-8">
<title>Kvt solutions — Business Card</title>
<link href="https://fonts.googleapis.com/css2?family=Arimo:ital,wght@0,400;0,700;1,700&display=swap" rel="stylesheet">
<style>
  :root {
    --backdrop: #151515;
    --brand-red: #c00010;
    --card-white: #ffffff;
    --ink: #000000;
    --on-red: #ffffff;
  }
  * { margin: 0; padding: 0; box-sizing: border-box; }
  html, body {
    width: 1200px;
    height: 1000px;
    overflow: hidden;
    background: var(--backdrop);
    font-family: "Arimo", Arial, sans-serif;
  }
  .canvas {
    position: relative;
    width: 1200px;
    height: 1000px;
  }
  .card {
    position: absolute;
    left: 51px;
    top: 164px;
    width: 1110px;
    height: 673px;
    background: var(--card-white);
  }
  .card__front-band {
    position: absolute;
    left: 0;
    top: 0;
    width: 100%;
    height: 494px;
    background: var(--brand-red);
  }
  .brand {
    position: absolute;
    left: 156px;
    top: 128px;
    color: var(--on-red);
  }
  .brand__name {
    font-size: 56px;
    font-weight: 700;
    line-height: 1;
    letter-spacing: 1px;
  }
  .brand__tagline {
    margin-top: 28px;
    margin-left: 66px;
    font-size: 16.5px;
    font-weight: 700;
    letter-spacing: 0.6px;
    text-transform: uppercase;
  }
  .person {
    position: absolute;
    right: 66px;
    top: 402px;
    text-align: right;
  }
  .person__name {
    color: var(--on-red);
    font-size: 33px;
    font-weight: 400;
    letter-spacing: 1px;
    word-spacing: 6px;
    line-height: 1.1;
    text-transform: uppercase;
  }
  .person__role {
    color: var(--ink);
    font-size: 27px;
    font-weight: 700;
    font-style: italic;
    line-height: 1.1;
  }
  .contact {
    position: absolute;
    right: 68px;
    top: 545px;
    text-align: right;
    color: var(--ink);
    font-size: 19px;
    line-height: 26px;
    word-spacing: 3px;
  }
</style>
</head>
<body>
  <main class="canvas">
    <section class="card" aria-label="Business card for Martin Oakes, Kvt solutions">
      <div class="card__front-band"></div>

      <div class="brand">
        <div class="brand__name">Kvt solutions</div>
        <div class="brand__tagline">Health &amp; Social Services Consulting</div>
      </div>

      <div class="person">
        <p class="person__name">Martin Oakes</p>
        <p class="person__role">Principal</p>
      </div>

      <address class="contact" style="font-style: normal;">
        <p class="contact__address">14 Wexcombe Ave, Larkdale VIC 3189</p>
        <p class="contact__lines">T: 0417 382 914 E: martino@kvtsolutions-example.com.au W: www.kvtsolutions-example.com.au</p>
      </address>
    </section>
  </main>
</body>
</html>
```